life insurance quote website design for lepontdoriole.ca

the web site lepontdoriole.ca need a design. we dont like the actuel one but we are open at all new suggestion. visit us at lepontdoriole.ca and you will understand. the principal concurant is tarifsgarantisnord.ca, calculeo.ca, coutprotecfam.ca. We are a life insurance quote site. we found best price available in the canadien industrie. We absolutly want a design with our form in the front page on the top right side like our concurance, we use wordpress at this time. we want to be able to switch language. and to have a logic form. we want to be able to change the color for each type of insurance quote page.we also need a blog in it to post news. and the site will be SEO accurate.

Target Market(s)

Get client fill the quote form

Industry/Entity Type

Insurance

Number of Pages Required

3 page

Font styles to use
Sans Serif

Requirements
Must have
• logic form on the top right first page
• page template for product info stuff, contact, and who we are, blog
• French site
• custum color
Nice to have
• Wordpress design will be appréciate
• switch language english/french

```html
<!DOCTYPE html>
<html lang="fr">
<head>
<meta charset="utf-8">
<title>Le Pont d'Oriole – Assurance vie</title>
<link href="https://fonts.googleapis.com/css2?family=Oswald:wght@400;500&family=Open+Sans:wght@400;600;700&display=swap" rel="stylesheet">
<style>
:root{
  --navy:#0b3f8c;
  --red:#e3101a;
  --red-dark:#b80910;
  --green-light:#8cc13a;
  --green-dark:#5b8d17;
  --heading:#0c3d7e;
  --text:#6d6d6d;
  --dark:#333333;
  --light-bg:#f1f1f1;
  --footer-bg:#f2f2f2;
  --line:#d9d9d9;
  --icon-blue:#1d4f91;
  --white:#ffffff;
}
*{margin:0;padding:0;box-sizing:border-box}
html,body{width:1200px;height:2329px;overflow:hidden}
body{position:relative;font-family:"Open Sans",Arial,sans-serif;color:var(--text);background:var(--white)}

/* header */
.site-header{position:absolute;left:0;top:0;width:1200px;height:102px;background:var(--navy)}
.brand{position:absolute;left:112px;top:34px;display:flex;align-items:center;gap:10px;color:var(--white);font-weight:700;font-size:17px}
.brand-dot{width:34px;height:34px;border-radius:50%;background:var(--red)}
.main-nav{position:absolute;left:0;top:0;width:1200px;height:102px}
.main-nav a{position:absolute;top:0;height:102px;line-height:106px;color:var(--white);text-decoration:none;font-size:11px;text-transform:uppercase;white-space:nowrap}
.main-nav a.active{background:var(--red);width:76px;text-align:center}
.lang-switch{position:absolute;left:1037px;top:41px;display:flex;align-items:center;gap:6px}

/* hero */
.hero{position:absolute;left:0;top:102px;width:1200px;height:423px;overflow:hidden}
.hero-photo{position:absolute;inset:0;background:linear-gradient(135deg,#8fb3cf 0%,#7ea58a 100%)}
.hero-panel{position:absolute;left:754px;top:0;width:446px;height:423px;background:rgba(26,94,170,.72);color:var(--white);font-family:"Oswald","Arial Narrow",sans-serif;text-transform:uppercase}
.hero-panel .tagline{position:absolute;left:50px;top:26px;font-size:42px;line-height:48px}
.hero-panel .phone{position:absolute;left:50px;top:196px;font-size:52px;letter-spacing:-1.5px;line-height:60px}
.hero-panel .area{position:absolute;left:50px;top:288px;font-size:42px;line-height:48px;letter-spacing:-.5px}
.hero-dots{position:absolute;left:563px;top:391px;display:flex;gap:7px}
.hero-dots span{width:11px;height:11px;border-radius:50%;background:rgba(255,255,255,.55)}
.hero-dots span.on{background:var(--white)}

/* intro */
.intro{position:absolute;left:0;top:525px;width:1200px;height:487px;background:var(--light-bg)}
.section-title{font-family:"Oswald","Arial Narrow",sans-serif;color:var(--heading);font-weight:400;text-transform:uppercase;font-size:28px;line-height:1}
.intro .section-title{position:absolute;left:110px;top:43px}
.body-text{font-size:11px;line-height:31px;color:var(--text);text-align:justify}
.intro .body-text{position:absolute;left:110px;top:87px;width:682px}
.product-list{position:absolute;left:110px;top:321px;width:682px}
.product{position:absolute;top:0;width:180px;text-align:center;font-size:11px;line-height:20px;color:var(--dark)}
.product .icon{width:70px;height:70px;border-radius:50%;background:#e2e2e2;margin:0 auto 16px;display:flex;align-items:center;justify-content:center}

.login-box{position:absolute;left:835px;top:80px;width:252px;height:259px;background:#e4e4e4;border-radius:3px}
.login-tab{position:absolute;left:36px;top:-11px;width:180px;height:53px;background:linear-gradient(#8d8d8d,#6c6c6c);color:var(--white);font-family:"Oswald","Arial Narrow",sans-serif;font-size:16px;text-align:center;line-height:53px;text-transform:uppercase;border-radius:2px}
.login-field{position:absolute;left:23px;width:204px;height:43px;background:var(--white);border:1px solid #d0d0d0;border-radius:3px;font-size:11px;color:#999;padding-left:14px;line-height:41px}
.login-submit{position:absolute;left:26px;top:175px;width:199px;height:45px;background:linear-gradient(var(--green-light),var(--green-dark));border-radius:3px;color:var(--white);font-family:"Oswald","Arial Narrow",sans-serif;font-size:15px;display:flex;align-items:center;justify-content:center;gap:6px;text-transform:uppercase}
.quote-button{position:absolute;left:835px;top:375px;width:252px;height:57px;background:linear-gradient(var(--red),var(--red-dark));border-radius:3px;color:var(--white);font-family:"Oswald","Arial Narrow",sans-serif;font-size:16px;text-align:center;line-height:57px;text-transform:uppercase}

/* how to */
.how{position:absolute;left:0;top:1012px;width:1200px;height:556px;background:var(--white);border-bottom:1px solid #e6e6e6}
.how .section-title{position:absolute;left:110px;top:46px;font-size:22px}
.how-image{position:absolute;left:110px;top:93px;width:309px;height:184px;border:4px solid #eeeeee;box-shadow:0 0 0 1px #d8d8d8;background:linear-gradient(135deg,#4a4d55 0%,#2b2e35 55%,#6c7078 100%)}
.how .text-side{position:absolute;left:446px;top:86px;width:642px}
.how .text-full{position:absolute;left:110px;top:302px;width:978px}
.more-link{position:absolute;left:110px;top:500px;font-family:"Oswald","Arial Narrow",sans-serif;color:var(--red);font-size:15px;text-transform:uppercase;display:flex;align-items:center;gap:6px}

/* blog */
.blog{position:absolute;left:0;top:1568px;width:1200px;height:432px}
.blog .section-title{position:absolute;left:110px;top:37px;font-size:22px}
.post{position:absolute;top:85px;width:226px}
.post-image{width:226px;height:151px;box-shadow:0 2px 3px rgba(0,0,0,.25)}
.post h3{font-weight:600;font-size:13.5px;color:var(--dark);margin-top:23px}
.post-meta{display:flex;gap:8px;font-size:10px;color:#777;margin-top:12px;align-items:center}
.post-meta span{display:flex;align-items:center;gap:3px}
.post p{font-size:10.4px;line-height:24px;color:#8a8a8a;text-align:justify;margin-top:5px}

/* footer */
.site-footer{position:absolute;left:0;top:2000px;width:1200px;height:251px;background:var(--footer-bg)}
.member-badge{position:absolute;left:110px;top:52px;width:232px;height:145px}
.member-badge .mark{position:absolute;left:0;top:0;width:84px;height:84px;background:#2a2a2a}
.member-badge .rule{position:absolute;left:0;top:106px;width:232px;height:2px;background:#333}
.divider{position:absolute;top:30px;width:1px;height:180px;background:var(--line)}
.footer-col{position:absolute;top:36px}
.footer-col h4{font-family:"Oswald","Arial Narrow",sans-serif;font-weight:400;font-size:16px;color:var(--dark);text-transform:uppercase;margin-bottom:10px}
.footer-col li{list-style:none;font-size:11px;color:#444;line-height:34.5px}
.office-title{font-size:11px;font-weight:700;color:#444;margin-top:14px}
.office-address{font-size:11px;color:#666;margin-top:6px}
.contact-line{display:flex;align-items:center;gap:14px;font-size:14px;color:#444;margin-top:10px}
.round-icon{width:42px;height:42px;border-radius:50%;background:var(--red);display:flex;align-items:center;justify-content:center}
.bottom-bar{position:absolute;left:0;top:2251px;width:1200px;height:78px;background:var(--navy);color:var(--white);font-size:11px}
.bottom-bar .legal{position:absolute;left:110px;top:32px}
.bottom-bar .copy{position:absolute;right:110px;top:32px}
</style>
</head>
<body>

<header class="site-header">
  <div class="brand"><span class="brand-dot"></span>lepontdoriole.ca</div>
  <nav class="main-nav">
    <a class="active" style="left:531px">Home</a>
    <a style="left:624px">Products</a>
    <a style="left:720px">Submission</a>
    <a style="left:824px">Who are we?</a>
    <a style="left:939px">Contact us</a>
  </nav>
  <div class="lang-switch">
    <svg width="32" height="20" viewBox="0 0 32 20"><rect width="32" height="20" fill="#1f3f8f"/><path d="M0 0L32 20M32 0L0 20" stroke="#fff" stroke-width="4"/><path d="M0 0L32 20M32 0L0 20" stroke="#d0202a" stroke-width="1.5"/><rect x="13" width="6" height="20" fill="#fff"/><rect y="7" width="32" height="6" fill="#fff"/><rect x="14.5" width="3" height="20" fill="#d0202a"/><rect y="8.5" width="32" height="3" fill="#d0202a"/></svg>
    <svg width="8" height="6" viewBox="0 0 8 6"><path d="M1 1l3 3 3-3" stroke="#fff" stroke-width="1.3" fill="none"/></svg>
  </div>
</header>

<section class="hero">
  <div class="hero-photo" role="img" aria-label="Photo d'une famille qui court main dans la main sur une pelouse devant des maisons"></div>
  <div class="hero-panel">
    <div class="tagline">Service rapide,<br>gratuit et<br>confidentiel</div>
    <div class="phone">1-855-555-0142</div>
    <div class="area">Nous desservons<br>tout le Quebec</div>
  </div>
  <div class="hero-dots"><span></span><span></span><span class="on"></span><span></span></div>
</section>

<section class="intro">
  <h1 class="section-title">Trouvez la meilleure assurance, au meilleur prix!</h1>
  <p class="body-text">Que vous soyez à la recherche d'une assurance vie, d'une assurance hypothécaire ou autre, vous désirez très certainement payer le prix le plus avantageux. S'y retrouver parmi les offres nombreuses du domaine de l'assurance peut être un véritable casse-tête. Mais grâce à l'intervention des conseillers en sécurité financière de Le Pont d'Oriole .ca, vous vous épargnerez des heures de recherche infructueuse, et, de plus, vous trouverez une police d'assurance qui vous convient, à un prix qui répond parfaitement aux contraintes de votre situation financière, quelle qu'elle soit. Nous utilisons une méthode novatrice, simple et efficace, qui vous permet de magasiner une police d'assurance dans le confort de votre logis grâce, notamment, à nos formulaires de soumission d'assurance en ligne. Le Pont d'Oriole .ca permet de trouver le meilleur prix pour une :</p>

  <div class="product-list">
    <div class="product" style="left:-11px">
      <div class="icon"><svg width="28" height="28" viewBox="0 0 28 28" fill="none" stroke="#555" stroke-width="2"><rect x="4" y="8" width="13" height="16" rx="1"/><path d="M10 8V4h9l5 5v12h-7"/><path d="M19 4v5h5"/></svg></div>
      Assurance vie permanente –<br>Assurance vie temporaire
    </div>
    <div class="product" style="left:177px">
      <div class="icon"><svg width="28" height="28" viewBox="0 0 28 28" fill="none" stroke="#555" stroke-width="2"><path d="M20 5H5v18h18V11"/><path d="M12 16l1-4 10-10 3 3-10 10z"/></svg></div>
      Assurance invalidité – Assur-<br>ance salaire
    </div>
    <div class="product" style="left:365px">
      <div class="icon"><svg width="28" height="28" viewBox="0 0 28 28" fill="none" stroke="#555" stroke-width="2"><rect x="4" y="6" width="20" height="18" rx="1"/><path d="M4 11h20M9 3v5M19 3v5"/><path d="M9 17l3 3 6-6"/></svg></div>
      Assurance prêt hypothécaire –<br>Assurance prêts
    </div>
    <div class="product" style="left:530px">
      <div class="icon"><svg width="26" height="26" viewBox="0 0 26 26"><path d="M4 13l6 6L22 7" stroke="#555" stroke-width="4" fill="none"/></svg></div>
      Assurance maladies<br>graves
    </div>
  </div>

  <form class="login-box">
    <div class="login-tab">Login here</div>
    <div class="login-field" style="top:57px">User Name</div>
    <div class="login-field" style="top:110px">Password</div>
    <div class="login-submit"><svg width="13" height="13" viewBox="0 0 14 14"><path d="M13 1L1 6l4 2 1 5 2-3 3 2z" fill="#fff"/></svg>Submit</div>
  </form>
  <div class="quote-button">Request a quote</div>
</section>

<section class="how">
  <h2 class="section-title">Comment procéder?</h2>
  <div class="how-image" role="img" aria-label="Photo d'une main tenant une bulle avec des icônes d'argent, de voiture et de famille"></div>
  <p class="body-text text-side">Il vous suffit de remplir le formulaire de soumission d'assurance en ligne ci-haut, en cliquant sous la catégorie d'assurance qui correspond à vos besoins. Dès que nous le recevrons, nous enverrons votre demande auprès de 21 différentes compagnies d'assurance afin de comparer les prix proposés. Nous avons accès aux produits des assureurs les plus reconnus au pays – ils détiennent 97 % de l'offre de l'assurance au Canada. Une fois votre demande soumise aux assureurs et les différentes options obtenues, nous vous mettrons en contact avec un conseiller en sécurité financière indépendant qui vous aidera à trouver la protection qui vous convient le mieux. Ceci vous permet d'obtenir rapidement les prix de plusieurs assureurs en toute simplicité de façon confidentielle et sans obligation de votre part.</p>
  <p class="body-text text-full">Des conseillers en sécurité financière compétents L'équipe de Le Pont d'Oriole .ca vous offre un service novateur dans le domaine de l'assurance. Grâce à nos méthodes éprouvées et à notre compétence, vous êtes assurés de trouver ce que vous cherchez, et même plus. Non seulement nous avons accès aux produits des assureurs les plus reconnus et les plus importants du Canada, mais de plus, nos conseillers en sécurité financière connaissent le domaine de l'assurance sur le bout des doigts. Ils sont au fait de toutes les lois et de tous les règlements en vigueur dans le domaine, et sauront magasiner pour vous une prime d'assurance avantageuse. En collaboration étroite avec vous, ils analyseront votre situation financière et vos besoins financiers. Ensemble, vous conviendrez d'un plan efficace et rentable pour les années à venir.<br>Vous aurez donc la certitude que vos produits d'assurances seront un bon investissement, effectué en toute connaissance de votre situation et de votre capacité financière.</p>
  <div class="more-link"><svg width="6" height="9" viewBox="0 0 6 9"><path d="M0 0l6 4.5L0 9z" fill="#e3101a"/></svg>Click more details</div>
</section>

<section class="blog">
  <h2 class="section-title">Our blog</h2>

  <article class="post" style="left:110px">
    <div class="post-image" role="img" aria-label="Photo d'un bureau avec un ordinateur portable et des documents" style="background:linear-gradient(135deg,#8a6b4a,#c9b497 50%,#5f6f7c)"></div>
    <h3>Lorem ipsum dolor sit amet</h3>
    <div class="post-meta"><span><svg width="11" height="10" viewBox="0 0 11 10"><path d="M1 1h9v6H5l-3 2V7H1z" fill="#1d4f91"/></svg>14</span><span><svg width="9" height="10" viewBox="0 0 9 10"><circle cx="4.5" cy="3" r="2.5" fill="#1d4f91"/><path d="M0 10c0-3 2-4.5 4.5-4.5S9 7 9 10z" fill="#1d4f91"/></svg>admin</span><span><svg width="10" height="10" viewBox="0 0 10 10"><circle cx="2" cy="5" r="1.6" fill="#1d4f91"/><circle cx="8" cy="2" r="1.6" fill="#1d4f91"/><circle cx="8" cy="8" r="1.6" fill="#1d4f91"/><path d="M2 5l6-3M2 5l6 3" stroke="#1d4f91"/></svg>Share</span></div>
    <p>Drug abuse prevention is beneficial to our entire society. Preventing substance abuse must start at an early age...</p>
  </article>

  <article class="post" style="left:362px">
    <div class="post-image" role="img" aria-label="Photo d'un expert remplissant un constat près d'une voiture accidentée" style="background:linear-gradient(135deg,#2e3a44,#7f909c 55%,#c8d2d8)"></div>
    <h3>Donec turpis nulla pulvinar</h3>
    <div class="post-meta"><span><svg width="11" height="10" viewBox="0 0 11 10"><path d="M1 1h9v6H5l-3 2V7H1z" fill="#1d4f91"/></svg>14</span><span><svg width="9" height="10" viewBox="0 0 9 10"><circle cx="4.5" cy="3" r="2.5" fill="#1d4f91"/><path d="M0 10c0-3 2-4.5 4.5-4.5S9 7 9 10z" fill="#1d4f91"/></svg>admin</span><span><svg width="10" height="10" viewBox="0 0 10 10"><circle cx="2" cy="5" r="1.6" fill="#1d4f91"/><circle cx="8" cy="2" r="1.6" fill="#1d4f91"/><circle cx="8" cy="8" r="1.6" fill="#1d4f91"/><path d="M2 5l6-3M2 5l6 3" stroke="#1d4f91"/></svg>Share</span></div>
    <p>Drug abuse prevention is beneficial to our entire society. Preventing substance abuse must start at an early age...</p>
  </article>

  <article class="post" style="left:612px">
    <div class="post-image" role="img" aria-label="Photo d'une main signant un contrat" style="background:linear-gradient(135deg,#5b7fa6,#b9c9da 55%,#e8edf2)"></div>
    <h3>Proin semper lorem</h3>
    <div class="post-meta"><span><svg width="11" height="10" viewBox="0 0 11 10"><path d="M1 1h9v6H5l-3 2V7H1z" fill="#1d4f91"/></svg>14</span><span><svg width="9" height="10" viewBox="0 0 9 10"><circle cx="4.5" cy="3" r="2.5" fill="#1d4f91"/><path d="M0 10c0-3 2-4.5 4.5-4.5S9 7 9 10z" fill="#1d4f91"/></svg>admin</span><span><svg width="10" height="10" viewBox="0 0 10 10"><circle cx="2" cy="5" r="1.6" fill="#1d4f91"/><circle cx="8" cy="2" r="1.6" fill="#1d4f91"/><circle cx="8" cy="8" r="1.6" fill="#1d4f91"/><path d="M2 5l6-3M2 5l6 3" stroke="#1d4f91"/></svg>Share</span></div>
    <p>Drug abuse prevention is beneficial to our entire society. Preventing substance abuse must start at an early age...</p>
  </article>

  <article class="post" style="left:862px">
    <div class="post-image" role="img" aria-label="Photo d'un conseiller présentant un document à un couple" style="background:linear-gradient(135deg,#d7d9dc,#a9b0b8 50%,#3c4754)"></div>
    <h3>Lorem ipsum dolor sit amet</h3>
    <div class="post-meta"><span><svg width="11" height="10" viewBox="0 0 11 10"><path d="M1 1h9v6H5l-3 2V7H1z" fill="#1d4f91"/></svg>14</span><span><svg width="9" height="10" viewBox="0 0 9 10"><circle cx="4.5" cy="3" r="2.5" fill="#1d4f91"/><path d="M0 10c0-3 2-4.5 4.5-4.5S9 7 9 10z" fill="#1d4f91"/></svg>admin</span><span><svg width="10" height="10" viewBox="0 0 10 10"><circle cx="2" cy="5" r="1.6" fill="#1d4f91"/><circle cx="8" cy="2" r="1.6" fill="#1d4f91"/><circle cx="8" cy="8" r="1.6" fill="#1d4f91"/><path d="M2 5l6-3M2 5l6 3" stroke="#1d4f91"/></svg>Share</span></div>
    <p>Drug abuse prevention is beneficial to our entire society. Preventing substance abuse must start at an early age...</p>
  </article>
</section>

<footer class="site-footer">
  <div class="member-badge" role="img" aria-label="Insigne de membre">
    <div class="mark"></div>
    <div class="rule"></div>
  </div>

  <div class="divider" style="left:377px"></div>
  <div class="divider" style="left:565px"></div>
  <div class="divider" style="left:728px"></div>

  <div class="footer-col" style="left:418px">
    <h4>Working hours</h4>
    <ul><li>Monday to Friday:</li><li>7am to 21hrs</li><li>Sunday:</li><li>10hrs to 15hrs</li></ul>
  </div>
  <div class="footer-col" style="left:599px">
    <h4>Quick links</h4>
    <ul><li>Products</li><li>Services</li><li>Contact Us</li><li>Send Mail</li></ul>
  </div>
  <div class="footer-col" style="left:778px">
    <h4>Contact</h4>
    <div class="office-title">The head office</div>
    <div class="office-address">48 Rue des Érables, Lachine, QC, H8S 1A1</div>
    <div class="contact-line"><span class="round-icon"><svg width="16" height="16" viewBox="0 0 16 16"><path d="M3 1l3 3-2 2c1 2 3 4 6 6l2-2 3 3-2 2C7 15 1 9 1 3z" fill="#fff"/></svg></span>1-855-555-0142</div>
    <div class="contact-line" style="margin-top:8px"><span class="round-icon"><svg width="16" height="12" viewBox="0 0 16 12"><rect width="16" height="12" rx="1" fill="#fff"/><path d="M1 1l7 6 7-6" stroke="#e3101a" stroke-width="1.5" fill="none"/></svg></span>contact@lepontdoriole.ca</div>
  </div>
</footer>

<div class="bottom-bar">
  <div class="legal">Privacy Policy &nbsp;|&nbsp; Sitemap</div>
  <div class="copy">Copyright@2016 Le Pont d'Oriole.All Right Reserved.</div>
</div>

</body>
</html>
```